bird wings, breathing, coaching, rhythm, heart

I would like this card design to be inspired by the following Rumi poem - now that I see some cards with the poem on it, I am pretty sure I don't want that. The feel of the cards should be watery and emotional, one of rhythm, breathing like a pendulum. An Ouroboros, (alchemical imagery in general), Birds, lungs, bird wings, hands, clouds, water, waves and rivers are all good images. Simple elegance is appreciated.
Cards should contain my name, title (coach), address, phone number and email address.
Your grief for what you've lost lifts a mirror
up to where you're bravely working.
Expecting the worst, you look, and instead,
here's the joyful face you've been wanting to see.
Your hand opens and closes and opens and closes.
If it were always a fist or always stretched open,
you would be paralyzed.
Your deepest presence
is in every small contracting and expanding,
the two as beautifully balanced and coordinated
as birdwings.
Contact Information for Business Card
Dorran Pelkwith, MA
Coach
4718 Varno St.
Berkeley, CA 94188
415-382-6649
pelkwith@mailvaro.net
Designer to choose colors to be used in the design.

```html
<!DOCTYPE html>
<html lang="en">
<head>
<meta charset="utf-8">
<title>Dorran Pelkwith, MA — Coach · Business Card</title>
<link rel="stylesheet" href="https://fonts.googleapis.com/css2?family=Gelasio:ital,wght@1,700&family=Roboto:wght@400&display=swap">
<style>
  :root {
    --backdrop: #2b2e33;
    --card-white: #fbfbfb;
    --ink: #1c1c1c;
    --ink-soft: #2a2a2a;
    --rule: #3a3a3a;
    --bird-grey: #5a5a5a;
    --water-deep: #2f7f8c;
    --water-mid: #6fc3c8;
    --water-light: #bfe6e4;
    --foam: #f4fbfb;
    --stone: #8fa3a6;
  }
  * { margin: 0; padding: 0; box-sizing: border-box; }
  html, body {
    width: 1200px;
    height: 900px;
    overflow: hidden;
    background: var(--backdrop);
  }
  .canvas {
    position: relative;
    width: 1200px;
    height: 900px;
  }
  .card {
    position: absolute;
    left: 300px;
    width: 600px;
    height: 343px;
    border-radius: 26px;
    overflow: hidden;
  }
  .card--front {
    top: 80px;
    background: var(--card-white);
    color: var(--ink);
  }
  .card--back {
    top: 477px;
  }

  .wire {
    position: absolute;
    left: 0;
    right: 0;
    top: 118px;
    height: 2px;
    background: var(--rule);
  }
  .identity {
    position: absolute;
    right: 40px;
    top: 34px;
    text-align: center;
  }
  .identity__name {
    font-family: "Gelasio", Georgia, serif;
    font-style: italic;
    font-weight: 700;
    font-size: 33px;
    letter-spacing: 0.2px;
    line-height: 1;
  }
  .identity__title {
    font-family: "Roboto", Arial, sans-serif;
    font-size: 20px;
    color: var(--ink-soft);
    margin-top: 8px;
    margin-left: 30px;
  }
  .birds-on-wire {
    position: absolute;
    left: 258px;
    top: 104px;
    width: 64px;
    height: 92px;
  }
  .address {
    position: absolute;
    left: 42px;
    top: 146px;
    font-family: "Roboto", Arial, sans-serif;
    font-size: 16px;
    line-height: 1.35;
    color: var(--ink-soft);
    text-align: center;
  }
  .contact {
    position: absolute;
    right: 64px;
    top: 254px;
    font-family: "Roboto", Arial, sans-serif;
    font-size: 17px;
    line-height: 1.35;
    color: var(--ink-soft);
    text-align: center;
  }
  .river-photo {
    position: absolute;
    inset: 0;
    background:
      radial-gradient(ellipse 22% 30% at 28% 22%, var(--stone) 0%, rgba(143,163,166,0) 100%),
      radial-gradient(ellipse 30% 60% at 8% 60%, var(--foam) 0%, rgba(244,251,251,0) 100%),
      linear-gradient(160deg, var(--water-deep) 0%, var(--water-mid) 38%, var(--water-light) 58%, var(--water-mid) 78%, var(--water-deep) 100%);
  }
</style>
</head>
<body>
<main class="canvas">
  <section class="card card--front" aria-label="Business card front">
    <div class="identity">
      <h1 class="identity__name">Dorran Pelkwith, MA</h1>
      <p class="identity__title">Coach</p>
    </div>
    <div class="wire"></div>
    <svg class="birds-on-wire" role="img" aria-label="Ink illustration of three small birds perched together on the wire" viewBox="0 0 64 92">
      <defs>
        <linearGradient id="birdInk" x1="0" y1="0" x2="0" y2="1">
          <stop offset="0" stop-color="var(--bird-grey)" stop-opacity="0.85"/>
          <stop offset="1" stop-color="var(--bird-grey)" stop-opacity="0.1"/>
        </linearGradient>
      </defs>
      <rect x="10" y="8" width="44" height="84" rx="14" fill="url(#birdInk)"/>
    </svg>
    <address class="address">
      4718 Varno St.<br>
      Berkeley, CA 94188
    </address>
    <div class="contact">
      415-382-6649<br>
      pelkwith@mailvaro.net
    </div>
  </section>

  <section class="card card--back" aria-label="Business card back">
    <div class="river-photo" role="img" aria-label="Photograph of clear turquoise river water flowing smoothly over a rounded stone"></div>
  </section>
</main>
</body>
</html>
```